The Lantern Guild Pitchdeck Template

The Lantern Guild would like a branded pitch deck template design for members to use when presenting their projects and proposals. The deck should include 10-15 different slide designs, each with the same branded theme, but with a variety of icon graphics and other design features that will empower members to easily create a beautiful pitch deck just by adding written content.

Please visit lanternguildhq.org to get a sense for our branding - purple, space, galaxy, white font and the planetary logo are some commonalities.

Here are 2 google drive links with some additional designs

https://files.boxmeadow.net/share/f/8QzrTa2Lk5VbNw7cHyP0dJe3sUmXg4RiF

https://files.boxmeadow.net/share/f/3Kd9-Rm6Tq2-yLvBn051fopwxhcT_zj7

```html
<!DOCTYPE html>
<html lang="en">
<head>
<meta charset="utf-8">
<title>The Lantern Guild – Pitch Deck Template</title>
<link rel="stylesheet" href="https://fonts.googleapis.com/css2?family=Montserrat:ital,wght@0,300;0,400;0,500;0,700;1,400&display=swap">
<style>
  :root {
    --page: #ffffff;
    --ink: #2b2b33;
    --ink-soft: #55555f;
    --rule: #a9a4c4;
    --white: #ffffff;
    --violet-deep: #2a1f5c;
    --violet: #5b3fa0;
    --night: #1b1d2a;
    --sky-blue: #8ea9c6;
    --sky-grey: #c9d3dd;
    --shadow: 0 6px 16px rgba(0,0,0,0.16);
  }
  * { box-sizing: border-box; margin: 0; padding: 0; }
  html, body { width: 1200px; height: 1060px; overflow: hidden; background: var(--page); }
  body { font-family: "Montserrat", sans-serif; color: var(--ink); position: relative; }

  .slide { position: absolute; width: 491px; height: 276px; overflow: hidden; box-shadow: var(--shadow); background: var(--white); }
  .slide--cover { left: 71px; top: 77px; }
  .slide--group { left: 640px; top: 77px; }
  .slide--intentions { left: 71px; top: 393px; }
  .slide--vision { left: 640px; top: 393px; }
  .slide--about { left: 71px; top: 709px; }
  .slide--partners { left: 640px; top: 709px; }

  .photo { position: absolute; }
  .eyebrow { font-size: 7.8px; letter-spacing: 2.4px; font-weight: 400; text-transform: uppercase; }
  .heading { font-size: 12.5px; font-weight: 400; letter-spacing: 0.6px; margin-top: 8px; }
  .rule { height: 1px; background: var(--rule); margin-top: 8px; }
  .footer { position: absolute; bottom: 7px; font-size: 5.6px; }
  .footer--left { left: 27px; }
  .footer--right { right: 30px; }

  .wordmark { font-weight: 700; letter-spacing: 4px; color: var(--white); }

  /* Cover */
  .cover-photo { inset: 0; background: radial-gradient(ellipse at 55% 25%, #e6ebf0 0%, var(--sky-grey) 40%, var(--sky-blue) 100%); }
  .cover-brand { position: absolute; left: 146px; top: 200px; }
  .cover-brand .wordmark { font-size: 36px; letter-spacing: 9px; }
  .cover-brand .tagline { color: var(--white); font-size: 9.5px; letter-spacing: 5px; margin-top: 4px; }
  .cover-url { position: absolute; right: 3px; top: 84px; height: 106px; writing-mode: vertical-rl; transform: rotate(180deg); color: var(--white); font-size: 7px; font-weight: 500; letter-spacing: 1.2px; white-space: nowrap; text-align: left; }

  /* Group */
  .group-photo { left: 0; top: 0; width: 254px; height: 276px; background: radial-gradient(ellipse at 50% 45%, var(--violet) 0%, #3b2a82 45%, var(--violet-deep) 100%); }
  .group-photo .wordmark { position: absolute; left: 75px; top: 122px; font-size: 18px; letter-spacing: 4px; }
  .group-photo .sub { position: absolute; left: 76px; top: 146px; color: var(--white); font-size: 4.5px; letter-spacing: 2px; }
  .group-text { position: absolute; left: 263px; top: 16px; width: 218px; }
  .group-text .eyebrow { color: var(--ink-soft); }
  .group-text .heading { font-size: 11.6px; letter-spacing: 0.1px; white-space: nowrap; }
  .group-text .rule { width: 212px; }
  .group-text .body { margin-top: 34px; width: 196px; font-size: 8.8px; line-height: 17.6px; }
  .slide--group .footer--left { color: var(--white); }

  /* Intentions */
  .intentions-photo { inset: 0; background: linear-gradient(180deg, var(--night) 0%, #242634 55%, #3a3428 100%); }
  .intentions-text { position: absolute; left: 0; right: 0; top: 16px; text-align: center; color: var(--white); }
  .intentions-text .rule { width: 212px; margin: 10px auto 0; background: #6b6b78; }
  .intentions-text .body { margin: 14px auto 0; width: 410px; font-size: 8.6px; line-height: 15.35px; }
  .slide--intentions .footer { color: var(--white); }

  /* Vision */
  .centered-head { position: absolute; left: 0; right: 0; top: 16px; text-align: center; }
  .centered-head .eyebrow { color: var(--ink-soft); }
  .centered-head .rule { width: 212px; margin: 10px auto 0; }
  .card { position: absolute; top: 74px; width: 130px; height: 158px; background: var(--white); box-shadow: 0 2px 6px rgba(0,0,0,0.18); text-align: center; }
  .card--people { left: 22px; }
  .card--planet { left: 180px; }
  .card--peace { left: 338px; }
  .card .photo { left: 0; top: 0; width: 130px; height: 90px; }
  .card--people .photo { background: linear-gradient(180deg, #8c7cc4 0%, #6b55a8 100%); }
  .card--planet .photo { background: radial-gradient(circle at 50% 50%, #6fa8c8 0%, #4d86b4 38%, #8f8fc9 62%, #c4c4e0 100%); }
  .card--peace .photo { background: linear-gradient(180deg, #e07aa0 0%, #f2a24a 55%, #f6c23a 100%); }
  .card h3 { position: absolute; top: 101px; left: 0; right: 0; font-size: 9.5px; font-weight: 700; letter-spacing: 1px; }
  .card p { position: absolute; top: 117px; left: 8px; right: 8px; font-size: 5.6px; line-height: 9.6px; font-style: italic; color: var(--ink-soft); }

  /* About */
  .about-text { position: absolute; left: 28px; top: 16px; width: 234px; }
  .about-text .eyebrow { color: var(--ink-soft); }
  .about-text .rule { width: 113px; }
  .about-text p { font-size: 8.5px; line-height: 16.7px; }
  .about-text .lead { margin-top: 12px; }
  .about-text .lead + p { margin-top: 8px; }
  .about-photo { left: 265px; top: 0; width: 226px; height: 276px; background: radial-gradient(ellipse at 40% 80%, #c7b6d9 0%, #8a6fae 35%, #4a3270 75%, #2c1f48 100%); }
  .about-photo .wordmark { position: absolute; left: 78px; top: 128px; font-size: 16px; letter-spacing: 3px; }
  .slide--about .footer--right { color: var(--white); }

  /* Partners */
  .partners-grid { position: absolute; left: 0; top: 0; width: 491px; height: 276px; }
</style>
</head>
<body>

<section class="slide slide--cover">
  <div class="photo cover-photo" role="img" aria-label="Photo of a white dove flying through bright clouds and rays of light"></div>
  <div class="cover-brand">
    <div class="wordmark">LANCI</div>
    <div class="tagline">LANTERN CIRCLE</div>
  </div>
  <div class="cover-url">www.lanternguildhq.org</div>
</section>

<section class="slide slide--group">
  <div class="photo group-photo" role="img" aria-label="Purple galaxy artwork of a thoughtful portrait in dotted star light">
    <div class="wordmark">LANCI</div>
    <div class="sub">LANTERN CIRCLE</div>
  </div>
  <div class="group-text">
    <div class="eyebrow">Lantern Circle</div>
    <h2 class="heading">A Group of Conscious Organisations</h2>
    <div class="rule"></div>
    <p class="body">Lantern Circle is a group of organisations that belong to The Lantern, and meet the standards defined by the Guild of what it means to be conscious. Non-profit, for the people, for the planet; creating a conscious economy.</p>
  </div>
  <div class="footer footer--left">Copyright © 2022 | All Rights Reserved</div>
  <div class="footer footer--right">Page | 02</div>
</section>

<section class="slide slide--intentions">
  <div class="photo intentions-photo" role="img" aria-label="Dark photo of hands working over glowing circuit lines"></div>
  <div class="intentions-text">
    <div class="eyebrow">Lantern Circle</div>
    <h2 class="heading">INTENTIONS</h2>
    <div class="rule"></div>
    <p class="body">The Lantern Guild, members, missionaries, stewards, sponsors, partners, and donors are working on various initiatives to fulfil our intentions. As a collective we are focusing on every area; from education, healthcare, economics, finance, governance &amp; technology, to space travel, art, music and transformational experiences. Our mission is to protect the Spirit of Air, Water, Land and Food; to create a system that supports the people and the planet; to redistribute wealth; protect human rights; serve justice and implement the conscious economy. We are focused on building a global community, transforming local environments, integration with Indigenous tribes and the reformation of society. We are interested in new paradigm schools and Universities, incubators for regenerative technology, natural medicine, empowering micro-industries, entrepreneurs, investors, inventors, artists and creatives. If you are involved in any initiative that benefits the collective, we would love to support you.</p>
  </div>
  <div class="footer footer--left">Copyright © 2022 | All Rights Reserved</div>
  <div class="footer footer--right">Page | 03</div>
</section>

<section class="slide slide--vision">
  <div class="centered-head">
    <div class="eyebrow">Lantern Circle</div>
    <h2 class="heading">WHAT WE ENVISION</h2>
    <div class="rule"></div>
  </div>
  <article class="card card--people">
    <div class="photo" role="img" aria-label="Photo of two children in a lavender field"></div>
    <h3>PEOPLE</h3>
    <p>A World that meets the needs of every human being as a birth right, providing the foundation for self-actualisation.</p>
  </article>
  <article class="card card--planet">
    <div class="photo" role="img" aria-label="Watercolour illustration of planet Earth"></div>
    <h3>PLANET</h3>
    <p>A World that lives in harmony with Nature; restore and protect Mother Earth, including the Animal Kingdom.</p>
  </article>
  <article class="card card--peace">
    <div class="photo" role="img" aria-label="Silhouette of a dove carrying an olive branch at sunset"></div>
    <h3>PEACE</h3>
    <p>A World that chooses peace, love and harmony, awake and aware of its connection with everything.</p>
  </article>
  <div class="footer footer--left">Copyright © 2022 | All Rights Reserved</div>
  <div class="footer footer--right">Page | 04</div>
</section>

<section class="slide slide--about">
  <div class="about-text">
    <div class="eyebrow">Lantern Circle</div>
    <h2 class="heading">WHO ARE WE</h2>
    <div class="rule"></div>
    <p class="lead">The Lantern Guild is a spiritual, conscious and regenerative non-profit organisation established for furthering the upliftment, enlightenment, spiritual realisation, and general welfare of people throughout the world, the betterment of life on planet Earth, and other spiritual, environmental, humanitarian, and beneficent purpose.</p>
    <p>Buddhism, Christianity, Hinduism, Islam, Judaism and other religions are belief systems; The Lantern exists whether you believe in it or not.</p>
  </div>
  <div class="photo about-photo" role="img" aria-label="Photo of a person sitting on a hill under a purple night sky">
    <div class="wordmark">LANCI</div>
  </div>
  <div class="footer footer--left">Copyright © 2022 | All Rights Reserved</div>
  <div class="footer footer--right">Page | 05</div>
</section>

<section class="slide slide--partners">
  <div class="centered-head">
    <div class="eyebrow">Lantern Circle</div>
    <h2 class="heading">PARTNERS</h2>
    <div class="rule"></div>
  </div>
  <svg class="partners-grid" viewBox="0 0 491 276" aria-label="Partner marks">
    <g stroke="#d6d6de" stroke-width="0.8">
      <line x1="130" y1="96" x2="130" y2="210"/>
      <line x1="234" y1="96" x2="234" y2="210"/>
      <line x1="348" y1="96" x2="348" y2="210"/>
      <line x1="50" y1="146" x2="122" y2="146"/>
      <line x1="140" y1="146" x2="226" y2="146"/>
      <line x1="243" y1="146" x2="340" y2="146"/>
      <line x1="357" y1="146" x2="449" y2="146"/>
    </g>
    <text x="80" y="121" text-anchor="middle" fill="#2a1f5c" font-family="Montserrat, sans-serif" font-weight="700" font-size="17" letter-spacing="3">LANCI</text>
    <rect x="170" y="103" width="26" height="26" fill="#3cb44a"/>
    <circle cx="290" cy="116" r="14" fill="#d9b15a"/>
    <circle cx="402" cy="116" r="20" fill="#4aa3c8"/>
    <circle cx="80" cy="176" r="12" fill="#3aa7c4"/>
    <circle cx="183" cy="176" r="13" fill="#4b2fe0"/>
    <circle cx="290" cy="176" r="20" fill="none" stroke="#3a3a3a" stroke-width="3"/>
    <circle cx="402" cy="176" r="18" fill="#111111"/>
  </svg>
  <div class="footer footer--left">Copyright © 2022 | All Rights Reserved</div>
  <div class="footer footer--right">Page | 06</div>
</section>

</body>
</html>
```